Kelvane Climate Business Card Design

Design new, 2 sides, business cards for a residential and light commercial heating, air conditioning contractor.

Target Market(s)

Homeowners, small businesses

Industry/Entity Type

Business

Contact Information for Business Card

Dominic Westerhall
Phone - 862-415-2736
Email
Address - PO box 518
Brightwater NJ 07912
Website - www.KelvaneClimateLLC.example

Requirements
Must have
• logo, company colors, standard size with no die cut, so I can use nova stamp

```html
<!DOCTYPE html>
<html lang="en">
<head>
<meta charset="utf-8">
<title>Kelvane Climate Business Card</title>
<link href="https://fonts.googleapis.com/css2?family=Lato:wght@400;700;900&display=swap" rel="stylesheet">
<style>
  :root {
    --maroon: #9c2234;
    --orange: #f29a1f;
    --ink: #5a5a5a;
    --rule: #9a9a9a;
    --paper: #ffffff;
    --backdrop: #e9e6e1;
  }
  * { box-sizing: border-box; margin: 0; padding: 0; }
  html, body { width: 1200px; height: 903px; overflow: hidden; }
  body { background: var(--backdrop); font-family: "Lato", sans-serif; position: relative; }

  .card {
    position: absolute;
    width: 540px;
    height: 309px;
    box-shadow: 0 10px 24px rgba(0,0,0,.25);
    overflow: hidden;
  }
  .card--front { left: 80px; top: 110px; background: var(--paper); }
  .card--back { left: 580px; top: 480px; background: var(--maroon); }

  .front-band { position: absolute; inset: 0; width: 100%; height: 100%; }

  .brand-name {
    position: absolute;
    font-weight: 900;
    line-height: 1.05;
    text-align: center;
    letter-spacing: .5px;
  }
  .card--front .brand-name {
    left: 24px; top: 105px; width: 180px;
    font-size: 30px; color: var(--maroon);
  }
  .card--back .brand-name {
    left: 0; right: 0; top: 100px;
    font-size: 40px; color: var(--orange);
  }

  .divider {
    position: absolute;
    left: 218px; top: 52px;
    width: 2px; height: 150px;
    background: var(--rule);
  }

  .contact { position: absolute; left: 240px; top: 46px; }
  .contact__name {
    font-size: 23px; font-weight: 700; color: var(--maroon);
    margin-bottom: 10px;
  }
  .contact__list { list-style: none; }
  .contact__item {
    display: flex; align-items: center; gap: 10px;
    font-size: 12.5px; color: var(--ink);
    height: 19px;
  }
  .contact__item svg { width: 14px; height: 14px; flex: none; fill: var(--orange); }
  .contact__item--address { align-items: flex-start; height: auto; margin-top: 14px; line-height: 1.35; font-size: 13.5px; }
  .contact__item--address svg { margin-top: 8px; }

  .back-url {
    position: absolute; left: 0; right: 0; bottom: 48px;
    text-align: center; font-size: 18px; color: var(--paper);
  }
  .back-url__domain { color: var(--orange); }
</style>
</head>
<body>

<section class="card card--front" aria-label="Business card front">
  <svg class="front-band" viewBox="0 0 540 309" preserveAspectRatio="none" aria-hidden="true">
    <polygon points="0,266 364,266 370,252 0,252" fill="var(--orange)" transform="translate(0,12)"/>
    <polygon points="0,280 368,280 388,220 540,220 540,309 0,309" fill="var(--maroon)"/>
  </svg>

  <div class="brand-name">Kelvane Climate</div>
  <div class="divider"></div>

  <div class="contact">
    <h1 class="contact__name">Dominic Westerhall</h1>
    <ul class="contact__list">
      <li class="contact__item">
        <svg viewBox="0 0 24 24"><path d="M6.6 10.8a15.1 15.1 0 0 0 6.6 6.6l2.2-2.2c.3-.3.7-.4 1-.2 1.1.4 2.3.6 3.6.6.6 0 1 .4 1 1V20c0 .6-.4 1-1 1A17 17 0 0 1 3 4c0-.6.4-1 1-1h3.5c.6 0 1 .4 1 1 0 1.3.2 2.5.6 3.6.1.3 0 .7-.2 1z"/></svg>
        862-415-2736
      </li>
      <li class="contact__item">
        <svg viewBox="0 0 24 24"><path d="M12 2a10 10 0 1 0 5 18.7l-1-1.7A8 8 0 1 1 20 12v1.5a1.5 1.5 0 0 1-3 0V12a5 5 0 1 0-1.5 3.5A3.5 3.5 0 0 0 22 13.5V12A10 10 0 0 0 12 2zm0 13a3 3 0 1 1 0-6 3 3 0 0 1 0 6z"/></svg>
        info@KelvaneClimateLLC.example
      </li>
      <li class="contact__item">
        <svg viewBox="0 0 24 24"><path d="M3 4h18v12H3zm2 2v8h14V6zM8 18h8v2H8z"/></svg>
        www.KelvaneClimateLLC.example
      </li>
      <li class="contact__item contact__item--address">
        <svg viewBox="0 0 24 24"><path d="M12 2a7 7 0 0 0-7 7c0 5 7 13 7 13s7-8 7-13a7 7 0 0 0-7-7zm0 9.5a2.5 2.5 0 1 1 0-5 2.5 2.5 0 0 1 0 5z"/></svg>
        <span>PO box 518<br>Brightwater NJ 07912</span>
      </li>
    </ul>
  </div>
</section>

<section class="card card--back" aria-label="Business card back">
  <div class="brand-name">Kelvane Climate</div>
  <p class="back-url">www.<span class="back-url__domain">KelvaneClimateLLC</span>.example</p>
</section>

</body>
</html>
```